TalkHarbor - Language Coaching Services

Sleek, innovative, trendy design for Language Coaching business.

TalkHarbor is a new UK based company that provides Language Coaching services. We offer highly personalized on-line and face to face language courses. We also impart learning techniques workshops based on the latest neuroscience research for second-language acquisition.

Target Market(s)

See attached info

Industry/Entity Type

Consulting

Contact Information for Business Card

TalkHarbor
DaniaKV@talkharbor.co.uk
TalkHarbor.co.uk
London, UK

Font styles to use
Sans Serif

```html
<!DOCTYPE html>
<html lang="en">
<head>
<meta charset="utf-8">
<title>TalkHarbor Business Card</title>
<link href="https://fonts.googleapis.com/css2?family=Montserrat:wght@400;600&family=Lato:wght@400&display=swap" rel="stylesheet">
<style>
  :root {
    --backdrop: #5c5c5c;
    --card-white: #ffffff;
    --brand-blue: #1a8fc9;
    --brand-blue-light: #0aa5dc;
    --brand-blue-deep: #0b7cbc;
    --ink: #4a4a4a;
    --divider: #9fd0ea;
  }
  * { margin: 0; padding: 0; box-sizing: border-box; }
  html, body { width: 1200px; height: 802px; overflow: hidden; }
  body { background: var(--backdrop); position: relative; font-family: "Lato", sans-serif; }

  .card {
    position: absolute; top: 274px; width: 442px; height: 265px;
    box-shadow: 2px 3px 6px rgba(0,0,0,0.45);
  }
  .card--front { left: 136px; background: var(--card-white); }
  .card--back { left: 624px; overflow: hidden; }

  .brand-mark { position: absolute; left: 85px; top: 83px; }
  .brand-name {
    position: absolute; left: 0; width: 225px; top: 158px; text-align: center;
    font-family: "Montserrat", sans-serif; font-weight: 400; font-size: 24px;
    letter-spacing: 0.5px; color: var(--brand-blue);
  }
  .divider {
    position: absolute; left: 225px; top: 78px; width: 1px; height: 111px;
    background: var(--divider);
  }
  .details { position: absolute; left: 243px; top: 75px; color: var(--ink); }
  .details__name {
    font-family: "Montserrat", sans-serif; font-size: 15px; color: var(--brand-blue);
    line-height: 18px;
  }
  .details__name strong { font-weight: 600; }
  .details__role, .details__place, .contact { font-size: 12.5px; line-height: 15px; }
  .details__place { margin-top: 9px; }
  .contacts { list-style: none; margin-top: 11px; }
  .contact { display: flex; align-items: center; gap: 4px; height: 16px; }
  .contact svg { flex: none; }

  .back-pattern {
    position: absolute; inset: 0;
    background: linear-gradient(120deg, var(--brand-blue-deep) 0%, var(--brand-blue-light) 45%, var(--brand-blue-deep) 70%, var(--brand-blue-light) 100%);
  }
  .back-name {
    position: absolute; left: 0; right: 0; top: 110px; text-align: center;
    font-family: "Montserrat", sans-serif; font-weight: 400; font-size: 36px;
    color: var(--card-white); letter-spacing: 0.5px;
  }
</style>
</head>
<body>
  <section class="card card--front">
    <svg class="brand-mark" width="72" height="72" viewBox="0 0 72 72" aria-hidden="true">
      <circle cx="36" cy="36" r="33" fill="none" stroke="var(--brand-blue)" stroke-width="5"/>
    </svg>
    <div class="brand-name">TALKHARBOR</div>
    <div class="divider"></div>
    <div class="details">
      <div class="details__name"><strong>MARCUS</strong> HALE</div>
      <div class="details__role">Managing Director</div>
      <div class="details__place">London, UK</div>
      <ul class="contacts">
        <li class="contact">
          <svg width="10" height="11" viewBox="0 0 10 11"><rect x="1.5" y="0.5" width="7" height="10" rx="1.5" fill="none" stroke="var(--brand-blue)" stroke-width="1.3"/></svg>
          044 777 1234
        </li>
        <li class="contact">
          <svg width="10" height="11" viewBox="0 0 10 11"><rect x="0" y="2" width="10" height="7" fill="var(--brand-blue)"/><path d="M0 2 L5 6 L10 2" fill="none" stroke="#fff" stroke-width="1"/></svg>
          DaniaKV@talkharbor.co.uk
        </li>
        <li class="contact">
          <svg width="10" height="11" viewBox="0 0 10 11"><circle cx="5" cy="5.5" r="5" fill="var(--brand-blue)"/></svg>
          www.TalkHarbor.co.uk
        </li>
      </ul>
    </div>
  </section>

  <section class="card card--back">
    <div class="back-pattern" role="img" aria-label="Repeating pattern of the brand symbol on a blue gradient"></div>
    <div class="back-name">TALKHARBOR</div>
  </section>
</body>
</html>
```